Valdane Companies Business Card Design

We need a new business card for our Private Equity Real Estate Development firm, “Valdane” and our EB-5 regional center “Thornmere Regional Center” on one card. We prefer a design that is simple, elegant, and represents the luxury products we design and build as well as the financial security and stability our successful history has produced. We are an industry leader in our field and 3rd generation family business that has evolved into an institutional quality investment platform. Considered design size is standard business card dimensions (3.5 x 2 inches with an additional 1/8 inch space for design elements or backgrounds that extend beyond the finished size of your piece.

Target Market(s)

• High net worth individuals
• Highly skilled technical workers and physicians in the US seeking investment-based immigration opportunities
• Sophisticated private equity investors
• Intermediary partners include domestic attorneys and investment brokers, as well as international agent networks
• US real estate developers

Industry/Entity Type

Finance

Contact Information for Business Card

(Providing placeholder info for personal information, please design for longer character spaces, longer names and addresses etc..)
• Logo for Valdane
• Logo for Thornmere Regional Center
• Full name: Marcus Valdane
• Job title: CEO
• Email address: mvaldane@valdanecompanies.com
• Cell phone number: +1.555.314.2287
• Office number +1.555.628.4410
• Office address: Larkfield Court 5, 4817 Vista Orilla, Elmbrook, NV.
• Website: www.valdanecompanies.com

Font styles to use
Serif
Sans Serif

Colors
ec1f27
ffffff
000000

Requirements
Must have
• • Logo for Valdane
• • Logo for Thornmere Regional Center
• - Use rounded corners
• (See .ai file included for logos)
Nice to have
• • Simple, elegant design
• • Aesthetically compatible with our website design (www.valdanecompanies.com)
• • Color palette including but not limited to white, black, and red (as per logos)
Should not have
• - Not too much red color
• - Do not stack both logos on top of each other

```html
<!DOCTYPE html>
<html lang="en">
<head>
<meta charset="utf-8">
<title>Valdane Companies Business Card</title>
<link href="https://fonts.googleapis.com/css2?family=Cinzel:wght@600;700&family=Open+Sans:wght@400&display=swap" rel="stylesheet">
<style>
  :root {
    --page-bg: #ecebe8;
    --card-white: #f7f7f6;
    --brand-red: #a3173a;
    --brand-red-bright: #c81f55;
    --ink: #111111;
    --text-grey: #555555;
    --divider: #cfcfcf;
    --card-dark-top: #2d2f31;
    --card-dark-bottom: #17181a;
    --white: #ffffff;
  }
  * { margin: 0; padding: 0; box-sizing: border-box; }
  html, body { width: 1200px; height: 960px; overflow: hidden; }
  body { background: var(--page-bg); position: relative; font-family: "Open Sans", Arial, sans-serif; }

  .card { position: absolute; border-radius: 18px; overflow: hidden; box-shadow: 0 3px 10px rgba(0,0,0,0.18); }

  .card-front { left: 302px; top: 128px; width: 600px; height: 342px; background: var(--card-white); }
  .card-front .edge-band {
    position: absolute; left: 0; right: 0; bottom: 0; height: 16px;
    background: linear-gradient(90deg, #7e1030, var(--brand-red-bright) 50%, #7e1030);
    border-top: 3px solid #d6d6d6;
  }

  .center-name { position: absolute; left: 34px; width: 240px; top: 98px; text-align: center; color: var(--brand-red); font-family: "Cinzel", Georgia, serif; font-weight: 700; }
  .center-name .mark-square { display: block; width: 48px; height: 48px; margin: 0 auto 16px; background: var(--brand-red); }
  .center-name .primary { display: block; font-size: 33px; line-height: 1; letter-spacing: 0.5px; }
  .center-name .secondary { display: block; font-size: 12px; letter-spacing: 4px; margin-top: 8px; }

  .divider { position: absolute; left: 290px; top: 74px; width: 1px; height: 194px; background: var(--divider); }

  .contact { position: absolute; left: 313px; top: 70px; }
  .contact .person-name { font-family: "Cinzel", Georgia, serif; font-weight: 600; font-size: 23px; color: var(--brand-red); letter-spacing: 0.5px; line-height: 1; }
  .contact .person-title { font-family: "Cinzel", Georgia, serif; font-weight: 600; font-size: 15px; color: var(--ink); margin-top: 3px; }
  .contact .address { margin-top: 5px; font-size: 14px; line-height: 19px; color: var(--text-grey); }
  .contact .lines { list-style: none; margin-top: 8px; font-size: 14px; line-height: 19px; color: var(--text-grey); }
  .contact .lines li { display: flex; align-items: center; gap: 8px; }
  .contact .lines svg { width: 14px; height: 14px; fill: var(--brand-red); flex: none; }

  .card-back { left: 298px; top: 497px; width: 602px; height: 343px; background: linear-gradient(160deg, var(--card-dark-top), var(--card-dark-bottom)); }
  .capital-name { position: absolute; left: 0; right: 0; top: 130px; display: flex; justify-content: center; align-items: center; gap: 20px; color: var(--white); font-family: "Cinzel", Georgia, serif; font-weight: 700; }
  .capital-name .mark-square { width: 64px; height: 64px; background: var(--white); }
  .capital-name .rule { width: 2px; height: 80px; background: var(--white); }
  .capital-name .words { display: flex; flex-direction: column; }
  .capital-name .primary { font-size: 44px; line-height: 1; }
  .capital-name .secondary { font-size: 14px; letter-spacing: 5px; margin-top: 8px; }
</style>
</head>
<body>
  <section class="card card-front">
    <div class="center-name">
      <span class="mark-square"></span>
      <span class="primary">THORNMERE</span>
      <span class="secondary">REGIONAL CENTER</span>
    </div>
    <div class="divider"></div>
    <div class="contact">
      <h1 class="person-name">MARCUS VALDANE</h1>
      <p class="person-title">CEO</p>
      <p class="address">Larkfield Court 5<br>4817 Vista Orilla<br>Elmbrook, NV.</p>
      <ul class="lines">
        <li><svg viewBox="0 0 16 16"><path d="M3.6 1l2.6 3-1.4 1.8c.9 2 2.5 3.6 4.4 4.5L11 8.9l3 2.5-1.4 2.8C7 14.4 1.6 9 1 3.1z"/></svg>+1.555.628.4410</li>
        <li><svg viewBox="0 0 16 16"><path d="M4 0h8a1 1 0 0 1 1 1v14a1 1 0 0 1-1 1H4a1 1 0 0 1-1-1V1a1 1 0 0 1 1-1zm1 2v10h6V2zm3 11a1 1 0 1 0 0 2 1 1 0 0 0 0-2z"/></svg>+1.555.314.2287</li>
        <li><svg viewBox="0 0 16 16"><path d="M1 3h14v1.2L8 9 1 4.2zm0 2.6l7 4.8 7-4.8V13H1z"/></svg>mvaldane@valdanecompanies.com</li>
        <li><svg viewBox="0 0 16 16"><circle cx="8" cy="8" r="7"/><path d="M1 8h14M8 1c-3 3-3 11 0 14M8 1c3 3 3 11 0 14" stroke="#f7f7f6" stroke-width="1.1" fill="none"/></svg>www.valdanecompanies.com</li>
      </ul>
    </div>
    <div class="edge-band"></div>
  </section>

  <section class="card card-back">
    <div class="capital-name">
      <span class="mark-square"></span>
      <span class="rule"></span>
      <div class="words">
        <span class="primary">VALDANE</span>
        <span class="secondary">CAPITAL</span>
      </div>
    </div>
  </section>
</body>
</html>
```